Stylish new business card needed!

Hello everyone! I am in need of a new business card design for an alarm company here in Hurricane WV. I have all fonts, color codes and logos provided for you use! We are a young company and like the style of a clean sleek looking business card. Would like it double sided, one side holding the logo and the other with your design!
Target Market(s)
The people that are looking for the newest tech for home automation and security
Industry/Entity Type
Alarm services; Home automation
Contact Information for Business Card
Name of person; position (Sales; Installer); Phone Number (555.418.7260); Employee cell Number; Website (www.GuardedByVelk.example); Employee Email; Double sided
Look and feel
Each slider illustrates characteristics of the customer's brand and the style your logo design should communicate.

```html
<!DOCTYPE html>
<html lang="en">
<head>
<meta charset="utf-8">
<title>Velk business card</title>
<link href="https://fonts.googleapis.com/css2?family=Arimo:wght@400;700&display=swap" rel="stylesheet">
<style>
  :root {
    --stage: #2b2b2e;
    --card: #1e1e22;
    --orange: #e8833f;
    --grey: #9a9a9c;
    --white: #f2f2f2;
    --ghost: #141417;
  }
  * { box-sizing: border-box; margin: 0; padding: 0; }
  html, body { width: 1200px; height: 780px; overflow: hidden; }
  body {
    background: var(--stage);
    font-family: "Arimo", Arial, sans-serif;
    position: relative;
  }
  .card {
    position: absolute;
    top: 235px;
    width: 540px;
    height: 309px;
    background: var(--card);
    overflow: hidden;
    border-radius: 2px;
  }
  .card--front { left: 45px; }
  .card--back { left: 615px; }

  .brand { position: absolute; left: 34px; top: 30px; }
  .brand__name {
    color: var(--orange);
    font-weight: 700;
    font-size: 30px;
    letter-spacing: 1px;
    text-transform: uppercase;
    line-height: 1;
  }
  .brand__tagline {
    margin-top: 8px;
    color: var(--orange);
    font-weight: 700;
    font-size: 9px;
    letter-spacing: 0.6px;
    text-transform: uppercase;
  }

  .contact { position: absolute; left: 34px; top: 118px; list-style: none; }
  .contact__item {
    display: flex;
    align-items: center;
    gap: 9px;
    color: var(--white);
    font-size: 13px;
    line-height: 21px;
  }
  .contact__icon { width: 12px; height: 12px; flex: none; }

  .person { position: absolute; right: 40px; top: 110px; text-align: right; }
  .person__name { font-size: 26px; font-weight: 700; color: var(--white); }
  .person__first { color: var(--orange); }
  .person__role { margin-top: 6px; font-size: 15px; color: var(--white); }

  .edge-tab {
    position: absolute; right: 0; top: 168px;
    width: 14px; height: 56px; background: var(--orange);
  }

  .ghost-mark {
    position: absolute;
    right: 30px; bottom: -22px;
    font-size: 120px;
    font-weight: 400;
    color: var(--ghost);
    letter-spacing: 6px;
    line-height: 1;
    text-transform: uppercase;
  }

  .back-mark {
    position: absolute; inset: 0;
    display: flex; flex-direction: column;
    align-items: center; justify-content: center;
  }
  .back-mark__name {
    font-size: 46px; font-weight: 700;
    color: var(--ghost);
    text-transform: uppercase;
    letter-spacing: 2px;
  }
  .back-mark__tagline {
    margin-top: 12px;
    font-size: 10px; font-weight: 700;
    color: var(--ghost);
    text-transform: uppercase;
    letter-spacing: 0.8px;
  }
</style>
</head>
<body>

<section class="card card--front">
  <div class="brand">
    <p class="brand__name">Guarded by Velk</p>
    <p class="brand__tagline">Automation and security services</p>
  </div>

  <ul class="contact">
    <li class="contact__item">
      <svg class="contact__icon" viewBox="0 0 12 12"><path d="M2.5 1 L4.5 1 L5.2 3.4 L4 4.3 Q5 6.8 7.7 8 L8.6 6.8 L11 7.5 L11 9.5 Q10.5 11 9 11 Q1 9.8 1 2.5 Q1 1 2.5 1Z" fill="var(--orange)"/></svg>
      555.418.7260
    </li>
    <li class="contact__item">
      <svg class="contact__icon" viewBox="0 0 12 12"><rect x="3" y="0.8" width="6" height="10.4" rx="1" fill="none" stroke="var(--white)" stroke-width="1.1"/><circle cx="6" cy="9.5" r="0.6" fill="var(--white)"/></svg>
      555.418.7261
    </li>
    <li class="contact__item">
      <svg class="contact__icon" viewBox="0 0 12 12"><circle cx="6" cy="6" r="5" fill="none" stroke="var(--orange)" stroke-width="1.2"/><ellipse cx="6" cy="6" rx="2" ry="5" fill="none" stroke="var(--orange)" stroke-width="1"/><line x1="1" y1="6" x2="11" y2="6" stroke="var(--orange)" stroke-width="1"/></svg>
      www.GuardedByVelk.example
    </li>
    <li class="contact__item">
      <svg class="contact__icon" viewBox="0 0 12 12"><rect x="0.8" y="2.3" width="10.4" height="7.4" fill="var(--orange)"/><path d="M0.8 2.3 L6 6.5 L11.2 2.3" fill="none" stroke="var(--card)" stroke-width="1"/></svg>
      info@GuardedByVelk.example
    </li>
  </ul>

  <div class="person">
    <p class="person__name"><span class="person__first">Mara</span> Lindqvist</p>
    <p class="person__role">Sales; Installer</p>
  </div>

  <div class="edge-tab"></div>
  <p class="ghost-mark" aria-hidden="true">Velk</p>
</section>

<section class="card card--back">
  <div class="back-mark">
    <p class="back-mark__name">Guarded by Velk</p>
    <p class="back-mark__tagline">Automation and security services</p>
  </div>
</section>

</body>
</html>
```